Website for Dental Office - The Bright Arch Clinic

The bright arch clinic is a dental office offering cosmetic dentistry, general dentistry, and multi-specialty dental care all under one roof in our state-of-the-art cosmetic dental center. We are particularly striving to provide services that fit the need of the young generation. Thus, we hope to have a modern, professional concise website that represents our spirit.

*Should be able to switch from English to Chinese

6 sections besides homepage:
Home, Meet us, Services,
Patient Info, Cases&Reviews, Blog, Contact

The Services sections should contain multiple subsections such as cleaning and prevention, cosmetic dentistry, implant dentistry, removable dentures, etc...
The Patient Info section is also intended to contain several subsections such as
New Patient offer, accepted Insurance, patient portal, helpful tips, etc...

Target Market(s)

young generation

Coding

Coded - Design and coding required

Number of Pages Required

5+ page

Font styles to use
Sans Serif

Colors
0592cd
33a6d7
85cae6
00a990
33b8a4
86cfc6
cee9f5
cfeae6
3277b5

Requirements
Must have
• *Should be able to switch from English to Chinese
Nice to have
• http://www.thebrightarchclinic.com/
• As a reference, the above link is the current website, but we would like to change the appearance and the content (our new logo's picture is attached)

```html
<!DOCTYPE html>
<html lang="en">
<head>
<meta charset="utf-8">
<title>The Bright Arch Clinic</title>
<link href="https://fonts.googleapis.com/css2?family=Roboto:ital,wght@0,400;0,500;0,700;0,900;1,400&display=swap" rel="stylesheet">
<style>
:root{
  --blue:#0592cd;
  --blue-2:#33a6d7;
  --blue-3:#85cae6;
  --blue-pale:#cee9f5;
  --navy:#3277b5;
  --ink:#1d1d1d;
  --text:#6b6b6b;
  --star:#f5a623;
  --footer:#0e0e0e;
  --white:#fff;
}
*{margin:0;padding:0;box-sizing:border-box}
html,body{width:1200px;height:4508px;overflow:hidden}
body{font-family:"Roboto",Arial,sans-serif;color:var(--ink);background:var(--white);position:relative}
.abs{position:absolute}
.btn{display:inline-flex;align-items:center;gap:10px;height:38px;padding:0 22px;border-radius:19px;font-size:12px;font-weight:700;letter-spacing:.5px;text-transform:uppercase;background:var(--blue);color:var(--white);white-space:nowrap}
.btn .arrow{width:16px;height:16px;border-radius:50%;background:var(--white);display:inline-flex;align-items:center;justify-content:center}
.btn-outline{background:var(--white);color:var(--blue);border:1px solid var(--blue-3)}
.btn-outline .arrow,.btn-light .arrow{background:var(--blue)}
.btn-light{background:var(--white);color:var(--blue)}
.section-title{font-size:40px;font-weight:900;text-align:center;text-transform:uppercase;width:100%}
.dots{display:flex;gap:8px;justify-content:center;width:100%}
.dots i{width:10px;height:10px;border-radius:50%;border:2px solid var(--blue-2);display:block}
.dots i.on{background:var(--blue-2)}

/* header */
.site-header{top:0;left:0;width:1200px;height:60px;background:var(--white);display:flex;align-items:center;justify-content:space-between;padding:0 112px}
.brand{display:flex;align-items:center;gap:10px;font-size:16px;font-weight:700;color:var(--blue)}
.brand .mark{width:28px;height:28px;background:var(--blue);border-radius:4px}
.main-nav{display:flex;align-items:center;gap:18px;font-size:12px;font-weight:700;color:var(--ink)}
.main-nav .active{background:var(--blue);color:var(--white);padding:7px 16px;border-radius:14px}
.lang{display:flex;align-items:center;gap:6px}
.lang .dot{width:16px;height:16px;border-radius:50%;background:var(--navy)}

/* hero */
.hero{top:60px;left:0;width:1200px;height:560px;background:linear-gradient(90deg,#3b4a55 0%,#7f8e98 40%,#c9d3d8 70%,#e7ecee 100%)}
.hero-copy{left:112px;top:270px;width:520px;color:var(--white)}
.hero-copy h1{font-size:42px;font-weight:900;text-transform:uppercase;margin-bottom:14px}
.hero-copy p{font-size:15px;line-height:1.5;margin-bottom:30px}

/* about */
.about-photo{left:112px;top:716px;width:448px;height:332px;border-radius:10px;background:linear-gradient(135deg,#d9ecf5,#8ccbe6 60%,#5aa7c9);box-shadow:0 8px 24px rgba(0,0,0,.15)}
.about-copy{left:640px;top:720px;width:448px}
.about-copy h2{font-size:40px;font-weight:900;text-transform:uppercase;margin-bottom:18px}
.about-copy p{font-size:14px;line-height:1.7;color:var(--text);text-align:justify;margin-bottom:30px}

/* services */
.services-band{top:1120px;left:0;width:1200px;height:848px;background:linear-gradient(180deg,#fff 0%,#f3f9fc 60%,#fff 100%)}
.service-card{top:1328px;width:304px;height:444px;background:var(--white);border-radius:8px;box-shadow:0 6px 20px rgba(0,0,0,.12);text-align:center;overflow:hidden}
.service-card .photo{height:206px;background:linear-gradient(135deg,#f3e1dc,#d98e8e 55%,#a24f55)}
.service-card .icon{width:52px;height:52px;border-radius:50%;background:var(--blue);border:4px solid var(--white);margin:-26px auto 0;position:relative;display:flex;align-items:center;justify-content:center}
.service-card h3{font-size:15px;font-weight:700;text-transform:uppercase;margin:18px 0 12px}
.service-card p{font-size:12px;line-height:1.6;color:var(--text);padding:0 28px;margin-bottom:22px}

/* patient info */
.patient{top:1968px;left:0;width:1200px;height:472px;background:linear-gradient(120deg,var(--blue-2),var(--blue) 70%);color:var(--white);text-align:center}
.patient h2{font-size:40px;font-weight:900;text-transform:uppercase;margin:96px 0 26px}
.patient p{font-size:13px;line-height:1.7;width:740px;margin:0 auto 34px}

/* blog */
.blog-card{background:var(--white);border-radius:8px;box-shadow:0 6px 20px rgba(0,0,0,.12);overflow:hidden}
.date{position:absolute;top:0;left:12px;background:var(--blue);color:var(--white);font-size:12px;font-weight:500;padding:8px 14px;display:flex;gap:6px;align-items:center}
.blog-card h3{font-size:20px;font-weight:900;text-transform:uppercase;margin-bottom:12px}
.blog-card p{font-size:13px;line-height:1.6;color:var(--text);margin-bottom:20px}

/* reviews */
.review{left:288px;top:3592px;width:616px;height:336px;background:var(--white);border-radius:6px;box-shadow:0 6px 22px rgba(0,0,0,.12)}
.avatar{left:48px;top:96px;width:104px;height:104px;border-radius:50%;background:linear-gradient(135deg,#d6d6d6,#8f8f8f)}
.review-copy{left:200px;top:72px;width:360px}
.review-copy q{display:block;font-style:italic;font-size:14px;line-height:1.7;color:var(--text);margin-bottom:16px}
.review-copy .name{font-size:13px;font-weight:700;text-transform:uppercase}
.stars{left:424px;top:222px;display:flex;gap:4px}
.arrow-nav{top:3740px;font-size:32px;color:var(--ink)}

/* footer */
.site-footer{top:4108px;left:0;width:1200px;height:400px;background:var(--footer);color:var(--white)}
.footer-brand{top:88px;left:0;width:1200px;display:flex;justify-content:center;align-items:center;gap:14px;font-size:26px;font-weight:700}
.footer-brand .mark{width:44px;height:44px;background:var(--blue);border-radius:6px}
.footer-col{top:196px}
.footer-col h4{font-size:13px;font-weight:700;text-transform:uppercase;margin-bottom:14px}
.footer-col li{list-style:none;font-size:12px;color:#d2d2d2;margin-bottom:9px;display:flex;gap:8px;align-items:flex-start}
.footer-col li::before{content:"›";color:var(--white)}
.footer-col.find li::before{content:none}
.footer-col svg{flex:none;margin-top:1px}
.footer-bar{top:346px;left:112px;width:976px;border-top:1px solid #2c2c2c;padding-top:16px;display:flex;justify-content:space-between;align-items:center;font-size:11px;color:#bdbdbd}
.social{display:flex;gap:14px}
.social i{display:block;width:14px;height:14px;border-radius:50%;background:#d6d6d6}
</style>
</head>
<body>

<header class="site-header abs">
  <div class="brand"><span class="mark"></span>The Bright Arch Clinic</div>
  <nav class="main-nav">
    <span class="active">HOME</span><span>MEET US</span><span>SERVICES</span><span>PATIENT INFO</span><span>CASES &amp; REVIEWS</span><span>BLOG</span><span>CONTACT</span>
    <span class="lang"><span class="dot"></span>ENG ▾</span>
  </nav>
</header>

<section class="hero abs" role="img" aria-label="Photo of a smiling child having a dental check-up with a dentist"></section>
<div class="hero-copy abs">
  <h1>The Bright Arch Clinic</h1>
  <p>Northfield and Riverton specialists that inspire confidence, we offer cosmetic dentistry, general dentistry.</p>
  <span class="btn">Read more <span class="arrow"><svg width="8" height="8" viewBox="0 0 8 8"><path d="M2 1l3 3-3 3" stroke="#0592cd" stroke-width="1.6" fill="none"/></svg></span></span>
</div>
<div class="dots abs" style="top:552px"><i></i><i class="on"></i><i></i></div>

<div class="about-photo abs" role="img" aria-label="Photo of a dentist and assistant with a young patient in the chair"></div>
<div class="about-copy abs">
  <h2>About us</h2>
  <p>The Bright Arch Clinic where we specialize in General Cosmetic Dentistry, Dental Implants/Periodontics (Gum Surgery) Endodontics (Root Canal Treatment) and Reconstructive Dentistry for patients in Westbrook, Millhaven, Cedar Falls, Ashford, Lindale.</p>
  <span class="btn">Read more <span class="arrow"><svg width="8" height="8" viewBox="0 0 8 8"><path d="M2 1l3 3-3 3" stroke="#0592cd" stroke-width="1.6" fill="none"/></svg></span></span>
</div>

<div class="services-band abs"></div>
<h2 class="section-title abs" style="top:1216px">Our services</h2>

<article class="service-card abs" style="left:112px">
  <div class="photo" role="img" aria-label="Photo of a dental cleaning in progress"></div>
  <div class="icon"><svg width="22" height="22" viewBox="0 0 22 22"><path d="M5 4c3-2 5 0 6 0s3-2 6 0c2 2 1 6 0 8l-1 7c0 1-2 1-2 0l-1-5c0-1-2-1-2 0l-1 5c0 1-2 1-2 0l-1-7C4 10 3 6 5 4z" fill="#fff"/></svg></div>
  <h3>Cleaning and Prevention</h3>
  <p>Professional dental cleanings (oral prophylaxis) are usually performed by the dentist or a registered dental.</p>
  <span class="btn">Read more <span class="arrow"><svg width="8" height="8" viewBox="0 0 8 8"><path d="M2 1l3 3-3 3" stroke="#0592cd" stroke-width="1.6" fill="none"/></svg></span></span>
</article>
<article class="service-card abs" style="left:448px">
  <div class="photo" role="img" aria-label="Photo of a woman with a bright smile" style="background:linear-gradient(135deg,#f4ece6,#d9bfae 55%,#9c7a66)"></div>
  <div class="icon"><svg width="22" height="22" viewBox="0 0 22 22"><path d="M5 4c3-2 5 0 6 0s3-2 6 0c2 2 1 6 0 8l-1 7c0 1-2 1-2 0l-1-5c0-1-2-1-2 0l-1 5c0 1-2 1-2 0l-1-7C4 10 3 6 5 4z" fill="#fff"/></svg></div>
  <h3>Cosmetic Dentistry</h3>
  <p>Veneers are very thin pieces of tooth shaped porcelain that are custom made and bonded onto the front.</p>
  <span class="btn">Read more <span class="arrow"><svg width="8" height="8" viewBox="0 0 8 8"><path d="M2 1l3 3-3 3" stroke="#0592cd" stroke-width="1.6" fill="none"/></svg></span></span>
</article>
<article class="service-card abs" style="left:784px">
  <div class="photo" role="img" aria-label="Close-up photo of teeth with a dental implant" style="background:linear-gradient(135deg,#f7e3df,#e6a7a4 55%,#b8605e)"></div>
  <div class="icon"><svg width="22" height="22" viewBox="0 0 22 22"><path d="M5 4c3-2 5 0 6 0s3-2 6 0c2 2 1 6 0 8l-1 7c0 1-2 1-2 0l-1-5c0-1-2-1-2 0l-1 5c0 1-2 1-2 0l-1-7C4 10 3 6 5 4z" fill="#fff"/></svg></div>
  <h3>Implant Dentistry</h3>
  <p>Professional dental cleanings (oral prophylaxis) are usually performed by the dentist or a registered dental.</p>
  <span class="btn">Read more <span class="arrow"><svg width="8" height="8" viewBox="0 0 8 8"><path d="M2 1l3 3-3 3" stroke="#0592cd" stroke-width="1.6" fill="none"/></svg></span></span>
</article>
<div class="dots abs" style="top:1836px"><i class="on"></i><i></i><i></i></div>

<section class="patient abs">
  <h2>Patient information</h2>
  <p>Thank you for your trust in us. We look forward to working with you towards a healthy and beautiful smile. Prior to your first appointment, we request that you please download and complete The New Patient Form – Adults or The New Patient Form – Children (15 &amp; Under). We accept most insurance and all major credit cards. We also offer special financing through SmilePay Finance.</p>
  <span class="btn btn-light">Read more <span class="arrow"><svg width="8" height="8" viewBox="0 0 8 8"><path d="M2 1l3 3-3 3" stroke="#fff" stroke-width="1.6" fill="none"/></svg></span></span>
</section>

<h2 class="section-title abs" style="top:2584px">Latest blog</h2>

<article class="blog-card abs" style="left:112px;top:2704px;width:476px;height:584px">
  <div role="img" aria-label="Photo of a patient receiving dental treatment" style="height:300px;background:linear-gradient(135deg,#cfe6f3,#7fb6d6 55%,#3e7fa8)"></div>
  <span class="date"><svg width="12" height="12" viewBox="0 0 12 12"><rect x="1" y="2" width="10" height="9" rx="1" fill="none" stroke="#fff"/><path d="M1 5h10" stroke="#fff"/></svg>05 Aug 2019</span>
  <div style="padding:36px 40px 0">
    <h3>Lorem ipsum</h3>
    <p>There are many variations of passages of Lorem Ipsum available, but the majority have suffered alteration in some form, by injected humour.</p>
    <span class="btn btn-outline">Read more <span class="arrow"><svg width="8" height="8" viewBox="0 0 8 8"><path d="M2 1l3 3-3 3" stroke="#fff" stroke-width="1.6" fill="none"/></svg></span></span>
  </div>
</article>

<article class="blog-card abs" style="left:600px;top:2704px;width:484px;height:284px;display:flex">
  <div role="img" aria-label="Close-up photo of a dental tool at a tooth" style="width:236px;flex:none;background:linear-gradient(135deg,#f0d4cf,#d9817c 55%,#a44743)"></div>
  <span class="date">06 Aug 2019</span>
  <div style="padding:48px 28px 0">
    <h3>Popular belief</h3>
    <p>It is a long established fact that a reader will be distracted by the readable content.</p>
    <span class="btn btn-outline">Read more <span class="arrow"><svg width="8" height="8" viewBox="0 0 8 8"><path d="M2 1l3 3-3 3" stroke="#fff" stroke-width="1.6" fill="none"/></svg></span></span>
  </div>
</article>

<article class="blog-card abs" style="left:600px;top:3000px;width:484px;height:288px;display:flex">
  <div role="img" aria-label="Close-up photo of a mouth during a dental exam" style="width:236px;flex:none;background:linear-gradient(135deg,#eed6cf,#cf8a7f 55%,#8f4a42)"></div>
  <span class="date">07 Aug 2019</span>
  <div style="padding:48px 28px 0">
    <h3>Consectetur</h3>
    <p>Later words, combined with a handful of model sentence structures, to generate.</p>
    <span class="btn btn-outline">Read more <span class="arrow"><svg width="8" height="8" viewBox="0 0 8 8"><path d="M2 1l3 3-3 3" stroke="#fff" stroke-width="1.6" fill="none"/></svg></span></span>
  </div>
</article>

<h2 class="section-title abs" style="top:3496px">Reviews</h2>
<span class="arrow-nav abs" style="left:196px">‹</span>
<span class="arrow-nav abs" style="left:976px">›</span>
<div class="review abs">
  <div class="avatar abs" role="img" aria-label="Portrait photo of the reviewer"></div>
  <div class="review-copy abs">
    <q>The Bright Arch Clinic transformed my smile and helped me feel more confident! Overall, I was so pleased by the professional setting and the kindness of the staff.</q>
    <div class="name">Marisol Quint</div>
  </div>
  <div class="stars abs">
    <svg width="96" height="16" viewBox="0 0 96 16" fill="#f5a623"><path id="s" d="M8 0l2.4 5 5.4.6-4 3.7 1.1 5.4L8 12 3.1 14.7l1.1-5.4-4-3.7L5.6 5z"/><use href="#s" x="20"/><use href="#s" x="40"/><use href="#s" x="60"/><use href="#s" x="80"/></svg>
  </div>
</div>

<footer class="site-footer abs">
  <div class="footer-brand abs"><span class="mark"></span>The Bright Arch Clinic</div>
  <div class="footer-col abs" style="left:112px"><h4>Quick links</h4><ul><li>Home</li><li>About us</li><li>Services</li><li>Patient Info</li><li>Cases &amp; Reviews</li></ul></div>
  <div class="footer-col abs" style="left:376px"><h4>Other links</h4><ul><li>Blog</li><li>Contact</li><li>Terms &amp; Conditions</li><li>Privacy Policy</li><li>FAQ</li></ul></div>
  <div class="footer-col abs" style="left:624px"><h4>Other links</h4><ul><li>Cleaning and Prevention</li><li>Cosmetic Dentistry</li><li>Implant Dentistry</li><li>Removable Dentures</li></ul></div>
  <div class="footer-col find abs" style="left:880px"><h4>Find us on</h4><ul>
    <li><svg width="12" height="14" viewBox="0 0 12 14"><path d="M6 0a5 5 0 015 5c0 4-5 9-5 9S1 9 1 5a5 5 0 015-5z" fill="#0592cd"/><circle cx="6" cy="5" r="2" fill="#0e0e0e"/></svg><span>2260 Harbor Lane<br>Suite 12</span></li>
    <li><svg width="12" height="12" viewBox="0 0 12 12"><path d="M2 1l3 0 1 3-2 1a7 7 0 003 3l1-2 3 1v3c-6 0-9-3-9-9z" fill="#0592cd"/></svg>1 555 240 0142</li>
    <li><svg width="12" height="12" viewBox="0 0 12 12"><path d="M2 1l3 0 1 3-2 1a7 7 0 003 3l1-2 3 1v3c-6 0-9-3-9-9z" fill="#0592cd"/></svg>1 555 240 0187</li>
    <li><svg width="12" height="10" viewBox="0 0 12 10"><rect width="12" height="10" rx="1" fill="#0592cd"/><path d="M1 1l5 4 5-4" stroke="#0e0e0e" fill="none"/></svg>info@thebrightarchclinic.com</li>
  </ul></div>
  <div class="footer-bar abs">
    <span>Copyright @ 2019 The Bright Arch Clinic. All Rights Reserved</span>
    <span class="social"><i></i><i></i><i></i><i></i></span>
  </div>
</footer>

</body>
</html>
```